Harbor Loom Floors Letterhead

Letterhead used for business reasons. It must be editable and easy to use.

Address is 2715 W. Pelican Lane Cedar Cove FL 34187 - 727.382.6519

```html
<!DOCTYPE html>
<html lang="en">
<head>
<meta charset="utf-8">
<title>Harbor Loom Floors Letterhead</title>
<link href="https://fonts.googleapis.com/css2?family=Montserrat:wght@400;600&display=swap" rel="stylesheet">
<style>
  :root {
    --backdrop: #e4e4e6;
    --paper: #ffffff;
    --ink: #3a3a3a;
    --ink-soft: #5a5a5a;
    --accent: #d98a2b;
    --signature-tone: #e9e9e9;
  }
  * { box-sizing: border-box; margin: 0; padding: 0; }
  html, body { width: 1200px; height: 908px; overflow: hidden; }
  body {
    background: var(--backdrop);
    font-family: "Montserrat", Arial, sans-serif;
    color: var(--ink);
    position: relative;
  }
  .letterhead {
    position: absolute;
    left: 296px; top: 24px;
    width: 608px; height: 860px;
    background: var(--paper);
    box-shadow: 0 2px 10px rgba(0,0,0,0.12);
  }
  .brand {
    position: absolute; left: 56px; top: 72px;
    font-size: 22px; font-weight: 400;
    color: var(--accent);
    letter-spacing: 0.5px;
  }
  .recipient {
    position: absolute; left: 56px; top: 150px;
    font-size: 8.5px; line-height: 1.55; color: var(--ink-soft);
  }
  .recipient .name, .signoff .name { font-weight: 600; color: var(--ink); }
  .body-copy {
    position: absolute; left: 110px; top: 232px; width: 420px;
    font-size: 8.5px; line-height: 1.75; color: var(--ink-soft);
  }
  .body-copy p { margin-bottom: 14px; }
  .signoff {
    position: absolute; left: 236px; top: 520px;
    font-size: 8.5px; line-height: 1.55; color: var(--ink-soft);
  }
  .signature {
    display: block; width: 120px; height: 28px; margin: 8px 0 6px;
    background: var(--signature-tone); border-radius: 3px;
  }
  .footer {
    position: absolute; right: 36px; top: 758px;
    display: flex; align-items: center; gap: 18px;
    font-size: 10px; line-height: 1.7; color: var(--ink-soft);
  }
  .footer .address { font-style: normal; }
  .footer .divider { width: 1px; height: 36px; background: var(--accent); }
  .contact-line { display: flex; align-items: center; gap: 6px; white-space: nowrap; }
  .contact-line svg { width: 9px; height: 9px; flex: none; }
</style>
</head>
<body>
  <main class="letterhead">
    <div class="brand">Harbor Loom Floors</div>

    <div class="recipient">
      <div class="name">Dana Whitfield</div>
      <div>Director</div>
      <div>City, State, Zip Code</div>
    </div>

    <div class="body-copy">
      <p>Proin gravida nibh vel velit auctor aliquet. Aenean sollicitudin, lorem quis bibendum auctor, nisi elit consequat ipsum, nec sagittis sem nibh id elit. Duis sed odio sit amet nibh vulputate cursus a sit amet mauris. Morbi accumsan ipsum velit. Nam nec tellus a odio tincidunt auctor a ornare odio. Sed non mauris vitae erat consequat auctor eu in elit. Class aptent taciti sociosqu ad litora torquent per conubia nostra, per inceptos himenaeos. Mauris in erat justo. Nullam ac urna eu felis dapibus</p>
      <p>This is the studio's version of Lorem Ipsum. Proin gravida nibh vel velit auctor aliquet. Aenean sollicitudin, lorem quis bibendum auctor, nisi elit consequat ipsum, lit. Duis sed odio sit amet nibh vulputate cursus a sit amet mauris. Morbi</p>
      <p>Nullam ac urna eu felis dapibus condimentum sit amet a augue. Sed non neque elit. Sed ut imperdiet nisi. Proin condimentum fermentum nunc. Etiam pharetra, erat sed fermentum feugiat, velit mauris egestas quam.Nullam ac urna eu felis dapibus condimentum sit amet a augue. Sed non neque elit. Sed ut imperdiet nisi. Proin condimentum</p>
    </div>

    <div class="signoff">
      <div>Sincerely,</div>
      <span class="signature" role="img" aria-label="Handwritten signature of Evan Corley"></span>
      <div class="name">Evan Corley</div>
      <div>President / CEO</div>
    </div>

    <footer class="footer">
      <address class="address">
        <div>2715 W. Pelican Lane</div>
        <div>Cedar Cove FL 34187</div>
      </address>
      <span class="divider"></span>
      <div class="contacts">
        <div class="contact-line">
          <svg viewBox="0 0 10 10" aria-hidden="true"><circle cx="5" cy="5" r="5" fill="var(--accent)"/><path d="M3.2 2.6c.3-.2.6-.1.8.2l.4.7c.1.2 0 .4-.1.5l-.3.3c.3.6.7 1 1.3 1.3l.3-.3c.2-.1.4-.2.5-.1l.7.4c.3.2.4.5.2.8-.4.6-1 .8-1.7.4-1-.5-1.9-1.4-2.4-2.4-.3-.7-.2-1.3.3-1.8z" fill="#fff"/></svg>
          <span>727.382.6519</span>
        </div>
        <div class="contact-line">
          <svg viewBox="0 0 10 10" aria-hidden="true"><circle cx="5" cy="5" r="5" fill="var(--accent)"/><circle cx="5" cy="5" r="2.8" fill="none" stroke="#fff" stroke-width="0.8"/><path d="M2.2 5h5.6M5 2.2c-1.2 1.6-1.2 4 0 5.6M5 2.2c1.2 1.6 1.2 4 0 5.6" stroke="#fff" stroke-width="0.6" fill="none"/></svg>
          <span>www.harborloomfloors.com</span>
        </div>
      </div>
    </footer>
  </main>
</body>
</html>
```